Business cards for KORU Real Estate Holdings LLC

We need a cool, original business card design for a company based in the Washington DC metropolitan area. We are a new energetic and passionate Real Estate Investing Company that invests in all types of real estate; commercial, residential, industrial etc.

Our company color is Red since it reflects action, energy and speed; it is assertive confident, energizing, exciting, powerful, passionate and determined. So we would like business card communicate those qualities to the audience.

Our audiences are investors that want to invest with us, real estate sellers, buyers, and tenants who lease from us.

Our logo is attached

```html
<!DOCTYPE html>
<html lang="en">
<head>
<meta charset="utf-8">
<title>KORU Real Estate Holdings LLC – Business Card</title>
<link href="https://fonts.googleapis.com/css2?family=Oswald:wght@400;500;600&family=Roboto+Condensed:wght@400;500&display=swap" rel="stylesheet">
<style>
  :root{
    --bg:#d9d6d0;
    --card:#ffffff;
    --charcoal:#3a3a3c;
    --charcoal-dark:#2c2c2e;
    --ink:#3a3a3c;
    --muted:#6b6b6e;
    --red:#d12a2f;
  }
  *{margin:0;padding:0;box-sizing:border-box}
  html,body{width:1200px;height:682px;overflow:hidden;background:var(--bg)}
  .stage{width:1200px;height:682px;display:flex;align-items:center;justify-content:center}
  .card{
    position:relative;width:1050px;height:600px;background:var(--card);
    box-shadow:0 10px 30px rgba(0,0,0,.18);overflow:hidden;
    font-family:"Roboto Condensed",Arial,sans-serif;color:var(--ink);
  }
  .top-strip{position:absolute;left:0;top:0;width:100%;height:46px;background:var(--charcoal)}
  .brand{position:absolute;left:70px;top:110px;display:flex;align-items:center;gap:22px}
  .brand-dot{width:70px;height:70px;border-radius:50%;background:var(--red)}
  .brand-text{display:flex;flex-direction:column}
  .brand-name{font-family:"Oswald",Arial,sans-serif;font-weight:600;font-size:78px;line-height:1;letter-spacing:6px;color:var(--charcoal)}
  .brand-tagline{font-family:"Oswald",Arial,sans-serif;font-weight:400;font-size:22px;letter-spacing:3px;color:var(--red);margin-top:6px}
  .name-band{position:absolute;left:0;top:262px;width:100%;height:64px;display:flex}
  .name-block{background:var(--charcoal-dark);width:430px;display:flex;align-items:center;padding-left:70px}
  .name{font-family:"Oswald",Arial,sans-serif;font-weight:500;font-size:38px;letter-spacing:3px;color:#fff;text-transform:uppercase}
  .gap{width:24px}
  .title-block{flex:1;background:var(--charcoal);display:flex;align-items:center;justify-content:flex-end;padding-right:60px}
  .title{font-family:"Oswald",Arial,sans-serif;font-weight:400;font-size:26px;letter-spacing:4px;color:#fff;text-transform:uppercase}
  .avatar-tab{position:absolute;left:0;top:350px;width:56px;height:56px;background:var(--charcoal);display:flex;align-items:center;justify-content:center}
  .contacts{position:absolute;left:100px;top:350px;display:grid;grid-template-columns:300px 400px;row-gap:22px;column-gap:60px}
  .contact{display:flex;align-items:center;gap:14px;font-size:24px;letter-spacing:1.5px;color:var(--ink)}
  .contact svg{flex:none}
  .address-band{position:absolute;left:0;bottom:68px;width:100%;height:60px;background:var(--charcoal);display:flex;align-items:center;padding-left:70px;gap:16px}
  .address{font-size:24px;letter-spacing:1.5px;color:#fff}
  .bottom-strip{position:absolute;left:0;bottom:0;width:100%;height:40px;background:var(--charcoal)}
</style>
</head>
<body>
<main class="stage">
  <section class="card">
    <div class="top-strip"></div>

    <div class="brand">
      <div class="brand-dot"></div>
      <div class="brand-text">
        <span class="brand-name">KORU</span>
        <span class="brand-tagline">REAL ESTATE HOLDINGS LLC</span>
      </div>
    </div>

    <div class="name-band">
      <div class="name-block"><span class="name">Daniel Reyes</span></div>
      <div class="gap"></div>
      <div class="title-block"><span class="title">General Manager</span></div>
    </div>

    <div class="avatar-tab">
      <svg width="28" height="28" viewBox="0 0 24 24" fill="#fff" aria-hidden="true"><circle cx="12" cy="8" r="4.5"/><path d="M3 22c0-5 4-8 9-8s9 3 9 8z"/></svg>
    </div>

    <div class="contacts">
      <div class="contact">
        <svg width="22" height="22" viewBox="0 0 24 24" fill="var(--charcoal)" aria-hidden="true"><path d="M6.6 10.8a15 15 0 0 0 6.6 6.6l2.2-2.2a1 1 0 0 1 1-.25 11.4 11.4 0 0 0 3.6.57 1 1 0 0 1 1 1V20a1 1 0 0 1-1 1A17 17 0 0 1 3 4a1 1 0 0 1 1-1h3.5a1 1 0 0 1 1 1c0 1.25.2 2.45.57 3.6a1 1 0 0 1-.25 1z"/></svg>
        <span>012 555 0148</span>
      </div>
      <div class="contact">
        <svg width="22" height="22" viewBox="0 0 24 24" fill="var(--charcoal)" aria-hidden="true"><path d="M2 5h20v14H2z" fill="none" stroke="var(--charcoal)" stroke-width="2"/><path d="M2 5l10 8 10-8" fill="none" stroke="var(--charcoal)" stroke-width="2"/></svg>
        <span>daniel@koruholdings.com</span>
      </div>
      <div class="contact">
        <svg width="22" height="22" viewBox="0 0 24 24" aria-hidden="true"><rect x="6" y="2" width="12" height="20" rx="2" fill="none" stroke="var(--charcoal)" stroke-width="2"/><circle cx="12" cy="18" r="1.2" fill="var(--charcoal)"/></svg>
        <span>012 555 0148</span>
      </div>
      <div class="contact">
        <svg width="22" height="22" viewBox="0 0 24 24" fill="none" stroke="var(--charcoal)" stroke-width="2" aria-hidden="true"><circle cx="12" cy="12" r="10"/><path d="M2 12h20M12 2c3 3 3 17 0 20M12 2c-3 3-3 17 0 20"/></svg>
        <span>www.koruholdings.com</span>
      </div>
    </div>

    <div class="address-band">
      <svg width="22" height="26" viewBox="0 0 24 28" fill="#fff" aria-hidden="true"><path d="M12 0a9 9 0 0 0-9 9c0 7 9 19 9 19s9-12 9-19a9 9 0 0 0-9-9zm0 12.5A3.5 3.5 0 1 1 12 5.5a3.5 3.5 0 0 1 0 7z"/></svg>
      <span class="address">240 Harbor Lane, Suite 3, Arlington VA</span>
    </div>
    <div class="bottom-strip"></div>
  </section>
</main>
</body>
</html>
```